Stationery for Villa Marenta Design Hotel**

Who we are:

Wander on an isolated beach while breathing in the fresh, salty, sea air. Listen to the warm Pacific wind rustling through green palm trees as you walk to a pristine lagoon. Feel the delicious warmth of the sun kiss your skin; the beach is yours. At Villa Marenta you can experience a vacation in undisturbed, natural beauty. We have created a place for you to find new strength, relaxation, and inner harmony. We offer total rest to the experienced traveler from all over the world.

We are a brand new and smartly built design-hotel (under construction) close to a unique beach and a fantastic surf spot in Huatulco, Southwest Mexico.

As you can see in the attachments, we do have an established corporate design, but as for now still need a format for booklets for information around our hotel and things to do in the area, important numbers (we fill in the content for that one).

Our corporate colors:
green #64b445, brown #b07043, blue #0ab7cf, yellow # f9b02a and #fcc01a, navy #444f69
Corporate fonts:
Krub and Miller Banner.
For further information access:
www.villamarenta.example
https://slidevault.example/view/QmPxLwZrTyKsNbVcHdJe/

Social Media: VillaMarenta

Industry/Entity Type

Hotel

Font styles to use
Other font styles liked:
• Krub, Miller Banner

Requirements
Must have
• Stick to Logo Design, defined corporate elements, logo, colors, fonts and general touch and feel
Nice to have
• Who we are:

Our corporate colors:
Corporate fonts:
Krub and Miller Banner.
www.villamarenta.example

Social Media: VillaMarenta

```html
<!DOCTYPE html>
<html lang="en">
<head>
<meta charset="utf-8">
<title>Villa Marenta – Receipt</title>
<link href="https://fonts.googleapis.com/css2?family=Libre+Caslon+Text:wght@400;700&display=swap" rel="stylesheet">
<style>
  :root {
    --page-bg: #ececec;
    --paper: #ffffff;
    --ink: #1e1e1e;
    --muted: #6e6e6e;
    --gold: #e0a21f;
    --teal-light: #3cc4d2;
    --teal-dark: #0e7f8c;
    --dot: #2a2a2a;
  }
  * { box-sizing: border-box; margin: 0; padding: 0; }
  html, body { width: 960px; height: 1200px; overflow: hidden; }
  body {
    background: var(--page-bg);
    font-family: "Libre Caslon Text", Georgia, serif;
    color: var(--ink);
    position: relative;
  }
  .receipt {
    position: absolute;
    left: 90px; top: 82px;
    width: 780px; height: 1036px;
    background: var(--paper);
    box-shadow: 2px 3px 6px rgba(0,0,0,0.35);
  }
  .brand {
    position: absolute;
    left: 48px; top: 36px;
    width: 144px;
    display: flex; flex-direction: column; align-items: center;
  }
  .brand-square {
    width: 144px; height: 144px;
    border: 3px solid var(--gold);
  }
  .brand-name {
    margin-top: 10px;
    font-size: 17px;
    letter-spacing: 1px;
    color: var(--gold);
    white-space: nowrap;
  }
  .contact {
    position: absolute;
    left: 214px; top: 54px;
    list-style: none;
    font-size: 17px;
    color: var(--muted);
    line-height: 31px;
  }
  .contact li { display: flex; align-items: flex-start; }
  .contact svg { width: 16px; height: 16px; margin: 7px 10px 0 0; flex: none; }
  .contact .indent { padding-left: 26px; }
  .serial {
    position: absolute;
    left: 522px; top: 116px;
    font-size: 31px;
  }
  .title-badge {
    position: absolute;
    left: 234px; top: 251px;
    width: 310px; height: 54px;
    border-radius: 14px;
    background: linear-gradient(180deg, var(--teal-light), var(--teal-dark));
    color: #fff;
    font-size: 48px;
    line-height: 56px;
    text-align: center;
    letter-spacing: 0.5px;
  }
  .field {
    position: absolute;
    left: 48px;
    height: 50px;
    display: flex; align-items: baseline;
    font-size: 42px;
  }
  .field .label { margin-right: 10px; }
  .field .fill {
    flex: 1;
    height: 6px;
    background-image: radial-gradient(circle, var(--dot) 2px, transparent 2.4px);
    background-size: 9px 6px;
    background-repeat: repeat-x;
  }
  .field.blank .fill { margin-left: 0; }
  .sign {
    position: absolute;
    font-size: 40px;
  }
  .sign.cashier { left: 48px; top: 904px; }
  .sign.guest { left: 416px; top: 896px; }
</style>
</head>
<body>
  <main class="receipt">
    <div class="brand">
      <div class="brand-square"></div>
      <div class="brand-name">VILLA MARENTA</div>
    </div>

    <ul class="contact">
      <li>
        <svg viewBox="0 0 16 16"><rect width="16" height="16" rx="2" fill="var(--gold)"/><path d="M8 3a3 3 0 0 0-3 3c0 2.3 3 6 3 6s3-3.7 3-6a3 3 0 0 0-3-3z" fill="#fff"/><circle cx="8" cy="6" r="1.1" fill="var(--gold)"/></svg>
        Villa Marenta, Playa Serena,
      </li>
      <li class="indent">Huatulco, Oaxaca, Mexiko</li>
      <li>
        <svg viewBox="0 0 16 16"><rect width="16" height="16" rx="2" fill="var(--gold)"/><path d="M5 3.5l2 2-1 1.3c.7 1.4 1.8 2.5 3.2 3.2l1.3-1 2 2-1.2 1.5C8 12.3 3.7 8 3.5 4.7z" fill="#fff"/></svg>
        +52 1 (958) 555 0142
      </li>
      <li>
        <svg viewBox="0 0 16 16"><rect width="16" height="16" rx="2" fill="var(--gold)"/><rect x="3" y="4.5" width="10" height="7" fill="none" stroke="#fff" stroke-width="1.2"/><path d="M3 4.5l5 4 5-4" fill="none" stroke="#fff" stroke-width="1.2"/></svg>
        hello@villamarenta.example
      </li>
      <li>
        <svg viewBox="0 0 16 16"><rect width="16" height="16" rx="2" fill="var(--gold)"/><circle cx="8" cy="8" r="5" fill="none" stroke="#fff" stroke-width="1.1"/><ellipse cx="8" cy="8" rx="2.2" ry="5" fill="none" stroke="#fff" stroke-width="1"/><path d="M3 8h10" stroke="#fff" stroke-width="1"/></svg>
        www.villamarenta.example
      </li>
    </ul>

    <div class="serial">No.</div>

    <h1 class="title-badge">RECEIPTS</h1>

    <div class="field" style="top:347px; width:682px;"><span class="label">Name</span><span class="fill"></span></div>
    <div class="field" style="top:416px; width:684px;"><span class="label">Folio</span><span class="fill"></span></div>
    <div class="field" style="top:486px; width:690px;"><span class="label">Date</span><span class="fill"></span></div>
    <div class="field" style="top:556px; width:694px;"><span class="label">Room</span><span class="fill"></span></div>
    <div class="field blank" style="top:626px; width:700px;"><span class="fill"></span></div>
    <div class="field" style="top:696px; width:700px;"><span class="label">Concept</span><span class="fill"></span></div>
    <div class="field" style="top:766px; width:710px;"><span class="label">Total</span><span class="fill"></span></div>

    <div class="sign cashier">Cashier</div>
    <div class="sign guest">Guest’s Signature</div>
  </main>
</body>
</html>
```